Psychology and personal development service needs an awesome Web Design

Hi, we are Bright, Build & Bloom, a psychology and personal development service located in Melbourne Australia. We already have a website www.brightbuild&bloom.org but it is in great need of a makeover! We add to the website regularly with articles and so we need a space to archive these when they come off the main page, and we have products that we would like to sell internationally so we need a shop page that can convert currencies for international sales and calculate postage and handling. We have a Facebook page that we would like to link as well as a newsletter that we would like to archive on the website. We have just had a logo designed through sketch hive and would like to incorporate this into our website. We want something with high visual impact and uncluttered.
We also run workshops and events so need a tab for this.
Thanks for getting on board!

```html
<!DOCTYPE html>
<html lang="en">
<head>
<meta charset="utf-8">
<title>Bright, Build & Bloom</title>
<link href="https://fonts.googleapis.com/css2?family=Open+Sans:wght@300;400;600&display=swap" rel="stylesheet">
<style>
:root{
  --page:#f9eef5;
  --panel:#ffffff;
  --purple:#6b3f9c;
  --plum:#7a4a8e;
  --pink:#d0509a;
  --badge:#b45aa8;
  --teal:#2fb89c;
  --teal-light:#7fded0;
  --events-arrow:#a650a4;
  --events-bg:#f7ecf4;
  --text:#8a8a8a;
  --dark:#444;
  --rule:#e3dce2;
  --footer-bar:#2b2b2b;
  --link:#2f7fc1;
}
*{box-sizing:border-box;margin:0;padding:0}
html,body{width:1200px;height:2284px;overflow:hidden}
body{background:var(--page);font-family:"Open Sans",Arial,sans-serif;color:var(--text);position:relative}
.abs{position:absolute}

/* header */
.brand{left:99px;top:26px;display:flex;align-items:center;gap:14px}
.brand-dot{width:60px;height:60px;border-radius:50%;background:var(--plum)}
.brand-name{font-size:26px;font-weight:400;color:var(--plum);line-height:1.1;width:170px}
.social-top{left:737px;top:30px;display:flex;gap:8px}
.soc{width:34px;height:34px;border-radius:50%}
.s1{background:#3b5998}.s2{background:#2aa3d8}.s3{background:#333}.s4{background:#f07a1e}.s5{background:#e0302f}.s6{background:#5b9b3c}
.cart{left:1010px;top:31px;display:flex;align-items:center;gap:10px;font-size:15px;color:var(--dark)}
.cart-icon{width:34px;height:34px;border-radius:50%;background:#e0408f;display:flex;align-items:center;justify-content:center}
.nav{right:100px;top:98px;display:flex;gap:30px;font-size:15px;color:var(--purple)}
.nav .active{color:var(--pink)}

/* main panel */
.panel{left:99px;top:157px;width:1002px;height:1803px;background:var(--panel);box-shadow:0 2px 6px rgba(0,0,0,.12)}
.hero{left:0;top:0;width:1002px;height:439px;background:linear-gradient(100deg,#cfe6f5 0%,#bcdcf1 35%,#e9f2f5 55%,#f3e3c0 75%,#d9b48e 100%)}
.hero-copy{left:41px;top:128px;width:330px}
.hero-copy h1{font-size:42px;font-weight:400;color:var(--purple);line-height:1.2;margin-bottom:6px}
.hero-copy p{font-size:15px;line-height:22.5px;color:#333}
.dots{left:41px;top:298px;width:101px;height:22px;border-radius:11px;background:#555;display:flex;align-items:center;justify-content:space-evenly;padding:0 6px}
.dots span{width:10px;height:10px;border-radius:50%;background:#fff}
.dots span.on{background:#555;border:2px solid #fff}

.section-title{left:0;width:1002px;text-align:center;font-size:24px;font-weight:300;color:var(--pink)}
.rule{left:11px;width:980px;height:1px;background:var(--rule)}
.tiles{left:11px;width:980px;display:flex;justify-content:space-between}
.tile{width:230px;text-align:center}
.tile .pic{width:230px;height:199px}
.tile .cap{margin-top:12px;font-size:16px;color:var(--plum)}

.bar{height:51px;display:flex;align-items:center;justify-content:space-between;color:#fff;font-size:20px;padding-left:15px}
.bar .arrow{width:38px;height:51px;display:flex;align-items:center;justify-content:center}
.bar-articles{left:11px;top:837px;width:697px;background:var(--teal)}
.bar-articles .arrow{background:var(--teal-light)}
.bar-events{left:730px;top:837px;width:261px;background:var(--purple)}
.bar-events .arrow{background:var(--events-arrow)}

.article{left:11px;width:697px;height:209px;border:1px solid var(--rule);display:flex}
.article .pic{width:196px;height:207px;flex:none}
.article .body{padding:15px 20px 0 15px}
.title{font-size:18px;color:var(--plum);line-height:1.4}
.date{display:inline-block;margin-top:3px;background:var(--badge);color:#fff;font-size:11px;padding:3px 12px;line-height:18px}
.article p{margin-top:14px;font-size:13px;line-height:19px;color:var(--text)}
.actions{margin-top:12px;display:flex;gap:22px}

.events{left:730px;top:888px;width:261px;height:452px;background:var(--events-bg);padding:0 13px}
.event{padding:20px 0 0;height:151px;border-bottom:1px solid #e2cfdc}
.event:last-child{border-bottom:none}
.event .title{font-size:17px}
.event p{margin-top:10px;font-size:11.5px;line-height:16.5px;color:var(--text)}

.video-tag{right:8px;top:6px;background:var(--badge);color:#fff;font-size:16px;font-weight:600;letter-spacing:1px;padding:2px 9px}
.social-bottom{left:379px;top:1733px;display:flex;gap:14px}

/* footer */
.fcol{top:1990px}
.fcol h3{font-size:17px;font-weight:400;color:var(--plum);margin-bottom:14px}
.fcol p{font-size:12.5px;line-height:19.5px;color:var(--text)}
.fcol strong{display:block;font-size:13.5px;color:var(--dark);font-weight:600;margin-bottom:2px}
.more{display:block;margin-top:6px;font-size:12.5px;color:var(--link)}
.vline{top:1987px;width:1px;height:206px;background:#e0cfdc}
.field{width:208px;height:30px;border:1px solid #ccc;background:#fff;font-size:11.5px;color:#333;padding:6px 15px;margin-bottom:13px}
.submit{margin-left:136px;width:72px;height:30px;background:#6d6d6d;color:#fff;font-size:13px;font-weight:600;display:flex;align-items:center;justify-content:center}
.links{font-size:12.5px;line-height:27.5px;color:var(--text)}
.bottom-bar{left:0;top:2211px;width:1200px;height:73px;background:var(--footer-bar);color:#bbb;font-size:12.5px;display:flex;align-items:center;justify-content:center}
</style>
</head>
<body>

<header>
  <div class="abs brand"><span class="brand-dot"></span><span class="brand-name">Bright, Build &amp; Bloom</span></div>
  <div class="abs social-top">
    <span class="soc s1"></span><span class="soc s2"></span><span class="soc s3"></span><span class="soc s4"></span><span class="soc s5"></span><span class="soc s6"></span>
  </div>
  <div class="abs cart">
    <span class="cart-icon"><svg width="18" height="16" viewBox="0 0 18 16"><path d="M2 6h14l-2 8H4z" fill="#fff"/><path d="M5 6l4-4 4 4" stroke="#fff" stroke-width="1.6" fill="none"/></svg></span>
    <span>$00.00</span>
  </div>
  <nav class="abs nav">
    <span class="active">HOME</span><span>ABOUT US</span><span>SERVICES</span><span>EVENTS</span><span>BLOG</span><span>STORE</span><span>CONTACT US</span>
  </nav>
</header>

<main class="abs panel">
  <section class="abs hero" role="img" aria-label="Photo of a smiling woman with arms spread out in bright sunlight"></section>
  <div class="abs hero-copy">
    <h1>Welcome</h1>
    <p>Integer laoreet sollicitudin porttitor. Lorem ipsum dolor sit amet, consectetur adipiscing elit. Suspendisse a feugiat magna. Proin imperdiet ante id velit auctor, vitae ullamcorper.</p>
  </div>
  <div class="abs dots"><span class="on"></span><span></span><span></span><span></span></div>

  <h2 class="abs section-title" style="top:478px">OUR WORKSHOP</h2>
  <div class="abs rule" style="top:530px"></div>
  <div class="abs tiles" style="top:553px">
    <div class="tile"><div class="pic" role="img" aria-label="Photo of a man in a counselling session on a white sofa" style="background:linear-gradient(135deg,#e8e8e6,#b9c3cc 60%,#6d86a8)"></div><div class="cap">Mauris pharetra</div></div>
    <div class="tile"><div class="pic" role="img" aria-label="Photo of a woman with glasses writing notes" style="background:linear-gradient(135deg,#f2ede8,#dccbb7 60%,#b49a82)"></div><div class="cap">Praesent aliquet</div></div>
    <div class="tile"><div class="pic" role="img" aria-label="Photo of a young woman in a checked shirt on a city street" style="background:linear-gradient(135deg,#a9b4b8,#6d7275 55%,#8a4b3e)"></div><div class="cap">Sed suscipit blandit</div></div>
    <div class="tile"><div class="pic" role="img" aria-label="Photo of a woman working at a desk with a tablet" style="background:linear-gradient(135deg,#cfc4bd,#f1ecea 55%,#3a3c4c)"></div><div class="cap">Pellentesque molestie</div></div>
  </div>
  <div class="abs rule" style="top:804px"></div>

  <div class="abs bar bar-articles"><span>LATEST ARTICLES</span><span class="arrow"><svg width="10" height="16"><path d="M2 2l6 6-6 6" stroke="#fff" stroke-width="2" fill="none"/></svg></span></div>
  <div class="abs bar bar-events"><span>EVENTS</span><span class="arrow"><svg width="10" height="16"><path d="M2 2l6 6-6 6" stroke="#fff" stroke-width="2" fill="none"/></svg></span></div>

  <article class="abs article" style="top:901px">
    <div class="pic" role="img" aria-label="Photo of a woman holding a blank card" style="background:linear-gradient(180deg,#d9d9d9,#a8a8a8 70%,#5a5050)"></div>
    <div class="body">
      <div class="title">Aenean porta metus lorem, in gravida orci finibus in</div>
      <span class="date">Oct 29,14</span>
      <p>Pellentesque et lacus laoreet, blandit erat non, feugiat tortor. Aliquam sed dignissim velit, vitae tincidunt lectus. Integer laoreet sollicitudin porttitor. Lorem ipsum dolor sit amet, consectetur adipiscing elit. Suspendisse a feugiat magna. Proin imperdiet ante id velit auctor.</p>
      <div class="actions">
        <svg width="14" height="12"><path d="M0 3h4l6 6h4M0 9h4l6-6h4" stroke="#777" stroke-width="1.4" fill="none"/></svg>
        <svg width="14" height="12"><path d="M1 1h12v7H6l-3 3V8H1z" fill="#777"/></svg>
        <svg width="12" height="12"><path d="M6 1l5 6H8v4H4V7H1z" fill="none" stroke="#777" stroke-width="1.3"/></svg>
        <svg width="12" height="12"><path d="M6 11L1 5h3V1h4v4h3z" fill="none" stroke="#777" stroke-width="1.3"/></svg>
      </div>
    </div>
  </article>
  <article class="abs article" style="top:1130px">
    <div class="pic" role="img" aria-label="Photo of a bald man with glasses making a doubtful expression" style="background:linear-gradient(180deg,#cfcfcf,#a5a5a5 60%,#6a6a6a)"></div>
    <div class="body">
      <div class="title">Aenean porta metus lorem, in gravida orci finibus in</div>
      <span class="date">Oct 29,14</span>
      <p>Pellentesque et lacus laoreet, blandit erat non, feugiat tortor. Aliquam sed dignissim velit, vitae tincidunt lectus. Integer laoreet sollicitudin porttitor. Lorem ipsum dolor sit amet, consectetur adipiscing elit. Suspendisse a feugiat magna. Proin imperdiet ante id velit auctor.</p>
      <div class="actions">
        <svg width="14" height="12"><path d="M0 3h4l6 6h4M0 9h4l6-6h4" stroke="#777" stroke-width="1.4" fill="none"/></svg>
        <svg width="14" height="12"><path d="M1 1h12v7H6l-3 3V8H1z" fill="#777"/></svg>
        <svg width="12" height="12"><path d="M6 1l5 6H8v4H4V7H1z" fill="none" stroke="#777" stroke-width="1.3"/></svg>
        <svg width="12" height="12"><path d="M6 11L1 5h3V1h4v4h3z" fill="none" stroke="#777" stroke-width="1.3"/></svg>
      </div>
    </div>
  </article>

  <aside class="abs events">
    <div class="event"><div class="title">Donec sollicitudin nisi neque</div><span class="date">Oct 29,14</span><p>Suspendisse a feugiat magna. Proin imperdiet ante id velit auctor, vitae ullamcorper.</p></div>
    <div class="event"><div class="title">Donec sollicitudin nisi neque</div><span class="date">Oct 29,14</span><p>Suspendisse a feugiat magna. Proin imperdiet ante id velit auctor, vitae ullamcorper.</p></div>
    <div class="event"><div class="title">Donec sollicitudin nisi neque</div><span class="date">Oct 29,14</span><p>Suspendisse a feugiat magna. Proin imperdiet ante id velit auctor, vitae ullamcorper.</p></div>
  </aside>

  <h2 class="abs section-title" style="top:1375px">OUR STORE</h2>
  <div class="abs rule" style="top:1427px"></div>
  <div class="abs tiles" style="top:1450px">
    <div class="tile"><div class="pic" role="img" aria-label="Purple book cover with a basket icon overlay" style="background:linear-gradient(135deg,#8c6a9c,#7b5590)"></div><div class="cap">Mauris pharetra</div></div>
    <div class="tile"><div class="pic" role="img" aria-label="Photo of a printed guide book on a wooden table" style="background:linear-gradient(135deg,#8a7564,#5e4b3e)"></div><div class="cap">Praesent aliquet</div></div>
    <div class="tile"><div class="pic" role="img" aria-label="Photo of a DVD case with discs" style="background:linear-gradient(135deg,#f2f2f2,#cfd3d8 60%,#5b7fa8)"></div><div class="cap">Sed suscipit blandit</div></div>
    <div class="tile" style="position:relative"><div class="pic" role="img" aria-label="Video still of a smiling couple embracing" style="background:linear-gradient(135deg,#4d6f8a,#7a5a48 60%,#3a2c28)"></div><span class="abs video-tag">VIDEO</span><div class="cap">Pellentesque molestie</div></div>
  </div>
  <div class="abs rule" style="top:1701px"></div>
  <div class="abs social-bottom">
    <span class="soc s1"></span><span class="soc s2"></span><span class="soc s3"></span><span class="soc s4"></span><span class="soc s5"></span><span class="soc s6"></span>
  </div>
</main>

<footer>
  <div class="abs fcol" style="left:105px;width:230px">
    <h3>About Northvale Studio</h3>
    <p>Integer laoreet sollicitudin porttitor. Suspendisse a feugiat magna. Proin imperdiet ante id velit auctor, vitae ullamcorper purus finibus. Maecenas nec arcu felis. Quisque ut purus enim. Proin nec turpis orci.</p>
    <span class="more">Know more</span>
  </div>
  <div class="abs vline" style="left:352px"></div>
  <div class="abs fcol" style="left:378px;width:225px">
    <h3>Latest News</h3>
    <strong>Morbi sit amet consequat diam</strong>
    <p>Cras faucibus sapien at arcu dignissim interdum. Sed tempus leo nulla, eget auctor tortor pharetra a. Morbi et gravida tortor, vitae cursus odio amet felis eleifend molestie</p>
    <span class="more">Know more</span>
  </div>
  <div class="abs vline" style="left:626px"></div>
  <div class="abs fcol" style="left:652px;width:215px">
    <h3>Email Signup</h3>
    <div class="field">Name</div>
    <div class="field">Email ID</div>
    <div class="submit">SUBMIT</div>
  </div>
  <div class="abs vline" style="left:883px"></div>
  <div class="abs fcol links" style="left:912px;top:1992px">Home<br>About us<br>Services<br>Events<br>Blog<br>Store<br>Contact us</div>
  <div class="abs fcol links" style="left:1018px;top:1992px">My Account<br>My Cart<br>Checkout<br>Terms of Use<br>Privacy Policy<br>Sitemap</div>
  <div class="abs bottom-bar">Copyright &copy; 2014&nbsp;&nbsp; Bright Build and Bloom.&nbsp;&nbsp; All rights reserved.</div>
</footer>

</body>
</html>
```